Blogging Platform for Christian Missions

We need the main (one) page design for FaithTrailer. FaithTrailer is a blogging platform for people (missionaries) who work for Christian Mission organisations in various countries. It will provides an easy way for them to setup and maintain a blog that will have features specifically for missions.

There's a lot of work involved in creating a web page design so I am happy to receive many quick rough designs. I will select my favourite four or five designs and these can submit the full design.

Please see the attached wireframe. Please also see the attached logo.

Main colours
- black
- white
- grey
- red (see logo colour) can be used occasionally eg. titles
- another complementary colour - occasionally used

Photos uploaded by the missionaries will provide colour for the website.

It needs to be a clean design that is not cluttered. The main focus are the blog posts. The information on the side complements the blog. There are navigational options at the top and bottom. The FaithTrailer logo is not the main focus. The person's name (blog owner) is what needs to be most prominent.

I love the BrightKarnu design (http://www.brightkarnu.com/). I particularly like the soft design - light grey background, white background boxes for content. The focus is the content - text and photos. I also like the subtle use of breakout image - "Step into the Venture". I like the black navigation header and the black footer. I do not want a exact copy of the site but I'd like to use this concept .

I also like this Vexlo design (http://calm.vexlo.com/theme/preview/5194) because of the white box (and the shadow) for the content. I also like how the word "Quote" and the number of "notes" breaks out of the white content area (see attachment). I'd like to do this, if possible with the date. This is just a "nice to have" - definitely not essential. I don't like the font for the title in this example.

We have build a simple prototype already. I cautiously show this because I want the the design of this to be completely ignored. I used a free template. Along with the wireframe this prototype should an idea of what kind of content will be displayed but please don't look too much at it.
http://faithtrailer.org/blog/1

The design will be used to create a website using Plonkit. We will use zScriptor so feel free to suggest an animation or lightbox effect to make your design more dynamic. This is a nice to have.

Once we have our final design we will need to define the style for:
- h1 through h4 tags
- Paragraphs
- Lists
- Block quotes
- Italics, bolding and underlining
- Links, including active, hover and visited states

Please let me know what additional information you need. Also let me know if there is something I have not considered.

Target Market(s)

The target customers are mission workers aged 25-35 who will post blog entries. These posts will be read by their friends and family.

Industry/Entity Type

Build

Requirements
Must have
• Clean simple design. Must be inspired by the BrightKarnu (http://www.brightkarnu.com/) design without copying it.
Nice to have
• Design element that breaks out of the boxes. See the screenshot attached from the Vexlo site. Described more in the project overview.
Should not have
• Should not use fonts that are not web-friendly. Should not have features that will be difficult to implement using HTML/CSS.

```html
<!DOCTYPE html>
<html lang="en">
<head>
<meta charset="utf-8">
<title>FaithTrailer – Hannah Brooke</title>
<link href="https://fonts.googleapis.com/css2?family=Arimo:ital,wght@0,400;0,700;1,400&family=EB+Garamond:ital@1&display=swap" rel="stylesheet">
<style>
:root{
  --ink:#333;
  --muted:#8a8a8a;
  --soft:#b0b0b0;
  --red:#d7001d;
  --bar:#4a4a4a;
  --page:#e9e9e9;
  --white:#fff;
  --panel:#f3f3f3;
  --ribbon:#5b5b5b;
  --footer:#2a2a2a;
  --social-a:#3b5998;
  --social-b:#4aaee0;
}
*{box-sizing:border-box;margin:0;padding:0}
html,body{width:963px;height:1200px;overflow:hidden}
body{position:relative;background:var(--page);font-family:"Arimo",Arial,sans-serif;color:var(--ink)}
a{color:inherit;text-decoration:none}
.abs{position:absolute}

.topbar{left:0;top:0;width:963px;height:30px;background:var(--bar)}
.topnav{left:117px;top:0;display:flex;height:30px}
.topnav a{color:#fff;font-size:11px;line-height:30px;padding:0 9px;text-transform:uppercase}
.topnav a.active{background:var(--red)}
.account{right:118px;top:0;color:#fff;font-size:11px;line-height:30px}
.account span{margin:0 8px;color:#ccc}

.masthead{left:0;top:30px;width:963px;height:88px;background:var(--white)}
.brand{left:121px;top:52px;display:flex;align-items:center;gap:10px}
.brand-dot{width:36px;height:36px;border-radius:50%;background:var(--red)}
.brand-name{font-size:34px;font-weight:700;color:#555;letter-spacing:-.5px}
.search{left:652px;top:67px;width:181px;height:20px;border:1px solid #e2e2e2;background:#fff;font-size:9px;color:#bbb;padding:4px 8px}
.search svg{position:absolute;right:6px;top:3px}

.owner{left:125px;top:133px}
.owner h1{font-size:27px;font-weight:700;color:#4b4b4b}
.owner p{font-size:14px;color:#777;margin-top:2px}

.share{left:70px;top:210px;width:42px;background:#fff;border:1px solid #ddd;padding:4px 3px;text-align:center}
.share .count{border:1px solid #cfd8de;font-size:12px;font-weight:700;color:#31648f;height:26px;line-height:26px;background:#fff}
.share .count.big{font-size:16px;font-weight:400;color:#333}
.share .btn{margin:3px 0 9px;font-size:8px;height:13px;line-height:13px;color:#fff}
.share .btn.a{background:#7ab0cf}
.share .btn.b{background:var(--social-a);margin-bottom:0}

.content{left:110px;top:197px;width:519px;height:836px;background:var(--white);box-shadow:0 0 0 4px #dcdcdc,0 2px 8px rgba(0,0,0,.25)}
.post{position:absolute;left:26px;width:467px}
.post h2{font-size:21px;font-weight:400;color:#555}
.post h2.first{color:var(--red)}
.post .meta{font-size:9px;color:var(--soft);margin-top:2px;padding-bottom:6px;border-bottom:1px solid #eee}
.post p{font-size:9.6px;line-height:14.6px;color:#888;margin-top:8px}
.post p.lead{font-family:"EB Garamond",Georgia,serif;font-style:italic;font-size:20.5px;line-height:26.5px;color:#aaa;margin-top:10px}
.social{position:absolute;right:4px;top:2px;display:flex;gap:3px}
.social i{width:20px;height:20px;border-radius:3px;background:var(--social-a)}
.social i+i{background:var(--social-b)}
.photo{width:475px;height:200px;margin-left:-4px;margin-top:26px;border:3px solid #e0e0e0;background:linear-gradient(180deg,#c9a157 0%,#b98d52 35%,#8c2f35 55%,#6a2028 75%,#4a3a38 100%)}
.postbar{height:19px;background:#efefef;display:flex;justify-content:space-between;align-items:center;padding:0 14px 0 17px;font-family:"EB Garamond",Georgia,serif;font-style:italic;font-size:11px;color:#777}
.postbar .c{display:flex;align-items:center;gap:8px}
.postbar .more.red{color:var(--red)}
.divider{border-top:2px dotted #ddd}

.follow{left:652px;top:205px;display:flex;align-items:center;gap:10px;font-size:14px;color:#666}
.follow .ic{display:flex;gap:6px}
.follow i{width:21px;height:21px;border-radius:3px;background:var(--social-a)}
.follow i+i{background:var(--social-b)}

.widget{position:absolute;left:637px;width:213px;background:var(--panel);box-shadow:0 0 0 3px #dadada,0 2px 5px rgba(0,0,0,.2)}
.widget h3{position:relative;margin-left:-7px;width:236px;height:26px;background:var(--ribbon);color:#fff;font-size:12.5px;font-weight:400;line-height:26px;padding-left:20px}
.widget h3::after{content:"";position:absolute;left:0;bottom:-4px;width:100%;height:4px;background:linear-gradient(-45deg,transparent 3px,var(--ribbon) 0) 0 0/6px 4px,linear-gradient(45deg,transparent 3px,var(--ribbon) 0) 0 0/6px 4px}
.widget .body{padding:14px 12px 6px 18px;font-size:9.4px;line-height:13px;color:#555;text-align:justify}
.widget .foot{border-top:1px solid #ddd;margin:0 6px;padding:4px 12px 6px;font-size:9px;color:#aaa;text-decoration:underline}
.widget ul{list-style:none;text-align:left}
.widget li.dot{padding-left:16px;position:relative}
.widget li.dot::before{content:"";position:absolute;left:4px;top:5px;width:3px;height:3px;border-radius:50%;background:#999}
.avatar{float:left;width:90px;height:76px;background:#555;border:3px solid #ddd;margin:0 8px 4px 0}
.map{width:186px;height:88px;border:3px solid #ddd;background:linear-gradient(135deg,#e8e4da 0%,#f3efe6 50%,#e9c96a 51%,#f2e3b5 100%);margin-bottom:6px}

.pager{left:242px;top:1044px;display:flex;gap:7px}
.pager span{height:23px;min-width:28px;border:1px solid #ddd;background:#fff;font-size:10px;color:#aaa;text-align:center;line-height:21px}
.pager span.wide{width:55px}
.pager span.on{background:var(--red);color:#fff;border-color:var(--red);font-weight:700}

.footer{left:0;top:1077px;width:963px;height:123px;background:var(--footer)}
.fcol{position:absolute;top:10px;font-size:9.6px;color:#ccc}
.fcol h4{color:var(--red);font-size:9.6px;font-weight:700;margin-bottom:6px}
.fcol li{list-style:none;line-height:15px;padding-left:15px;position:relative}
.fcol li::before{content:"";position:absolute;left:2px;top:6px;width:3px;height:3px;border-radius:50%;background:#aaa}
.fbrand{left:640px;top:1126px;display:flex;align-items:center;gap:8px}
.fbrand .brand-dot{width:22px;height:22px;background:#fff}
.fbrand .brand-name{font-size:22px;color:#fff}
</style>
</head>
<body>
<div class="abs topbar"></div>
<nav class="abs topnav"><a class="active" href="#">Mission Blogs</a><a href="#">Opportunities</a><a href="#">Option3</a><a href="#">Option4</a></nav>
<div class="abs account">SIGN IN<span>|</span>REGISTER</div>

<header class="abs masthead"></header>
<div class="abs brand"><span class="brand-dot"></span><span class="brand-name">faithtrailer.org</span></div>
<div class="abs search">Search<svg width="12" height="12" viewBox="0 0 12 12"><circle cx="5" cy="5" r="3.6" fill="none" stroke="#777" stroke-width="1.5"/><line x1="7.6" y1="7.6" x2="11" y2="11" stroke="#777" stroke-width="1.8"/></svg></div>

<div class="abs owner"><h1>Hannah Brooke</h1><p>NorthRoad Australia</p></div>

<aside class="abs share">
  <div class="count">240</div><div class="btn a">Post</div>
  <div class="count big">257</div><div class="btn b">Share</div>
</aside>

<main class="abs content">
  <article class="post" style="top:14px">
    <h2 class="first">Just Arrived</h2>
    <div class="social"><i></i><i></i></div>
    <div class="meta">Submitted by Hannah Brooke on Mon, 14 April 2011 - 07:58</div>
    <p>Lorem ipsum dolor sit amet, consectetuer adipiscing elit. Aenean commodo ligula eget dolor. Aenean massa. Cum sociis natoque penatibus et magnis dis parturient montes, nascetur ridiculus mus. Donec quam felis, ultricies nec, pellentesque eu, pretium quis, sem. Nulla consequat massa quis enim. , justo. Nullam dictum felis eu pede mollis pretium. Integer tincidunt. Cras dapibus.</p>
    <p style="margin-top:16px">Enim. Aliquam lorem ante, dapibus in, viverra quis, feugiat a, tellus. Phasellus viverra nulla ut metus varius laoreet. Quisque rutrum. Aenean imperdiet. Etiam ultricies nisi vel augue. Curabitur ullamcorper ultricies nisi. Nam eget dui. Etiam rhoncus. Maecenas tempus, tellus eget condimentum  ricies nisi. Nam eget dui. Etiam rhoncus. Maecenas tempus, tellus eget condimentum</p>
    <div class="photo" role="img" aria-label="Photo of a living room with red sofas and a dark coffee table"></div>
    <div class="postbar" style="margin-top:13px"><span class="c"><svg width="11" height="9" viewBox="0 0 11 9"><path d="M0 0h11v6H5L2 9V6H0z" fill="#d7001d"/></svg>4 comments</span><span class="more red">Read more</span></div>
    <div class="divider" style="margin-top:10px"></div>
  </article>

  <article class="post" style="top:484px">
    <h2>Only 14 days to go before I fly for Malawi</h2>
    <div class="social" style="top:3px"><i></i><i></i></div>
    <div class="meta">Submitted by Hannah Brooke on Mon, 30 March 2011 - 09:00</div>
    <p class="lead">Lorem ipsum dolor sit amet, consectetuer adipiscing elit. Aenean commodo ligula eget dolor. Aenean massa. Cum sociis natoque penatibus et magnis dis parturient montes, nascetur ridiculus mus. Donec quam felis, ultricies nec,</p>
    <div class="postbar" style="margin-top:16px"><span class="c"><svg width="11" height="9" viewBox="0 0 11 9"><path d="M0 0h11v6H5L2 9V6H0z" fill="#d7001d"/></svg>4 comments</span><span class="more">Read more</span></div>
    <div class="divider" style="margin-top:8px"></div>
  </article>

  <article class="post" style="top:686px">
    <h2>Only 14 days to go before I fly for Malawi</h2>
    <div class="social" style="top:3px"><i></i><i></i></div>
    <div class="meta">Submitted by Hannah Brooke on Mon, 30 March 2011 - 09:00</div>
    <p>Lorem ipsum dolor sit amet, consectetuer adipiscing elit. Aenean commodo ligula eget dolor. Aenean massa. Cum sociis natoque penatibus et magnis dis parturient montes, Lorem ipsum dolor sit amet, consectetuer adipiscing elit. Aenean commodo ligula eget dolor. Aenean massa. Cum sociis natoque penatibus et magnis dis parturient montes, Lorem ipsum dolor sit amet, consectetuer adipiscing elit.</p>
    <div class="postbar" style="margin-top:9px"><span class="c"><svg width="11" height="9" viewBox="0 0 11 9"><path d="M0 0h11v6H5L2 9V6H0z" fill="#d7001d"/></svg>4 comments</span><span class="more">Read more</span></div>
  </article>
</main>

<div class="abs follow">Follow Hannah Brooke<span class="ic"><i></i><i></i></span></div>

<section class="widget" style="top:238px">
  <h3>About Hannah</h3>
  <div class="body" style="min-height:100px"><div class="avatar"></div>Lorem ipsum dolor sit amet, consectetuer adipiscing elit. Aenean commodo ligula eget dolor. odo ligula eget dolor. Aenean</div>
  <div class="foot">View my complete profile</div>
</section>

<section class="widget" style="top:409px">
  <h3>About Hannah's Ministry</h3>
  <div class="body">Lorem ipsum dolor sit amet, consectetuer adipiscing elit. Aenean commodo ligula eget dolor. Aenean Lorem ipsum dolor sit amet, consectetuer adipiscing elit. Aenean</div>
  <div class="foot">Read more</div>
</section>

<section class="widget" style="top:553px">
  <h3>About Malawi</h3>
  <div class="body"><div class="map" role="img" aria-label="Street map of a town in Malawi with a location pin"></div>Lorem ipsum dolor sit amet, consectetuer adipiscing elit. Aenean commodo ligula eget dolor. Aenean Lorem</div>
  <div class="foot">Read more</div>
</section>

<section class="widget" style="top:766px">
  <h3>NorthRoad Events</h3>
  <div class="body"><ul><li>NorthRoad Prayer Event - May 15th</li><li>NorthRoad Conference - June 30th</li></ul></div>
  <div class="foot">Read more</div>
</section>

<section class="widget" style="top:874px">
  <h3>NorthRoad Events</h3>
  <div class="body"><ul><li class="dot">Teacher in Blanta (2yrs)</li><li class="dot">Financial Controller (long term)</li><li class="dot">Project Manager (6months+)</li><li class="dot">Bible College Lecturer (long term)</li></ul></div>
  <div class="foot">Read more</div>
</section>

<nav class="abs pager"><span class="wide">Previous</span><span class="on">1</span><span>2</span><span>3</span><span>4</span><span>5</span><span class="wide">Next</span></nav>

<footer class="abs footer">
  <div class="fcol" style="left:125px"><h4>About Us</h4><ul><li>About FaithTrailer</li><li>Missionaries</li><li>Mission Agencies</li><li>Churches</li><li>Mission Supporters</li><li>Privacy</li></ul></div>
  <div class="fcol" style="left:255px"><h4>Regions Mission</h4><ul><li>Africa</li><li>Asia</li><li>North America</li><li>Latin America</li><li>Aust/Pacific</li></ul></div>
  <div class="fcol" style="left:405px"><h4>Agencies</h4><ul><li>CLM</li><li>Open Horizons</li><li>NorthRoad Australia</li><li>WMF</li></ul></div>
</footer>
<div class="abs fbrand"><span class="brand-dot"></span><span class="brand-name">faithtrailer.org</span></div>
</body>
</html>
```